Graphic Design Zephyrmart Book Description

There is a book on Zephyrmart that is my competitor that has a large graphic design as part of the description for the book and I want a similar thing for my book to make it stand out more.

My competitors book is here: https://www.zephyrmart.example/Stellar-Chemistry-Novices-Grasping-Walkthrough/dp/K47RTPW612/

My book is here: https://www.zephyrmart.example/Stellar-Chemistry-Groundwork-Reactions-Bonding/dp/K9HXCVT27S/

You can see the kind of thing I am looking for on the book listing but I have attached an image below.

Thanks

Trevor

```html
<!DOCTYPE html>
<html lang="en">
<head>
<meta charset="utf-8">
<title>Book Description Graphic</title>
<link rel="stylesheet" href="https://fonts.googleapis.com/css2?family=Bebas+Neue&family=Oswald:wght@300;700&family=Poppins:wght@400;500;600;800&display=swap">
<style>
  :root {
    --space-deep: #0f1a3a;
    --space-mid: #1d2752;
    --yellow: #ece42a;
    --yellow-soft: #e6dd3a;
    --red: #d4121a;
    --white: #ffffff;
    --ink: #111111;
    --navy: #0c1f5c;
    --cyan-glow: #3fd8ff;
    --card-border: #e2d93a;
    --pill-text: #3b3320;
  }
  * { box-sizing: border-box; margin: 0; padding: 0; }
  html, body { width: 723px; height: 1200px; overflow: hidden; background: #a7aeb3; }
  .canvas {
    position: relative; width: 723px; height: 1200px; overflow: hidden;
    background:
      radial-gradient(ellipse 80% 14% at 50% 34%, rgba(200,130,50,.55), transparent 70%),
      linear-gradient(180deg, var(--space-deep) 0%, var(--space-mid) 25%, #3a2c2a 38%, #1c2448 55%, #191a2c 75%);
    font-family: 'Poppins', sans-serif;
  }

  .headline { position: absolute; left: 366px; top: 42px; width: 350px; z-index: 3; }
  .headline span { display: block; white-space: nowrap; }
  .headline .lead { font-family: 'Bebas Neue', sans-serif; font-size: 64px; line-height: 54px; letter-spacing: 1px; color: var(--white); }
  .headline .accent { font-weight: 800; font-size: 32px; line-height: 26px; color: var(--yellow); }
  .headline .plain { font-weight: 800; font-size: 26px; line-height: 30px; color: var(--white); margin-top: 2px; }
  .headline .topic { font-weight: 800; font-size: 58px; line-height: 48px; letter-spacing: -1px; color: var(--navy);
    text-shadow: 0 0 6px var(--cyan-glow), 0 0 14px rgba(63,216,255,.7); }

  .book-stack { position: absolute; left: 80px; top: 84px; width: 272px; height: 300px;
    background: linear-gradient(170deg, #f2ea2c, #d8cf20); }
  .book-open { position: absolute; left: 196px; top: 315px; width: 329px; height: 228px;
    background: linear-gradient(160deg, #f4f4f4, #d6d6d6); transform: skewY(-4deg); }
  .book-back { position: absolute; left: 524px; top: 332px; width: 147px; height: 211px;
    background: linear-gradient(180deg, #f0e72e, #d4cb1f); }

  .badge-audience { position: absolute; left: 48px; top: 355px; width: 166px; height: 166px; border-radius: 50%;
    background: radial-gradient(circle at 40% 35%, #ec2a2a, var(--red) 70%); z-index: 2;
    display: flex; flex-direction: column; align-items: center; justify-content: center; text-align: center;
    font-weight: 800; font-size: 13.5px; line-height: 15px; color: var(--white); }
  .badge-audience .top { font-weight: 500; letter-spacing: 2px; }
  .badge-audience .hl { color: var(--yellow); }

  .badge-gift { position: absolute; left: 598px; top: 283px; width: 90px; height: 90px; border-radius: 50%;
    background: var(--red); transform: rotate(18deg); z-index: 2;
    display: flex; flex-direction: column; align-items: center; justify-content: center; text-align: center;
    color: var(--white); font-weight: 800; font-size: 8px; line-height: 1; }
  .badge-gift .big { font-family: 'Bebas Neue', sans-serif; font-size: 21px; color: var(--yellow); line-height: .85; }

  .features { position: absolute; left: 59px; top: 584px; display: flex; gap: 12px; }
  .feature { width: 143px; height: 246px; border: 1px solid var(--card-border); border-radius: 9px; overflow: hidden;
    background: linear-gradient(180deg, rgba(40,30,25,.92), rgba(18,14,12,.96)); }
  .feature.alt { border-color: #ddd; }
  .feature-title { height: 107px; background: var(--yellow); display: flex; flex-direction: column; align-items: center; justify-content: center;
    text-align: center; color: var(--ink); padding: 0 3px; }
  .feature.alt .feature-title { background: var(--white); }
  .feature-title .light { font-family: 'Oswald', sans-serif; font-weight: 300; font-size: 22px; line-height: 20px; }
  .feature-title .bold { font-family: 'Oswald', sans-serif; font-weight: 700; font-size: 21px; line-height: 20px; letter-spacing: -.3px; }
  .feature-text { padding: 10px 6px 0; text-align: center; color: var(--white); font-size: 12.3px; line-height: 15.8px; }

  .yellow-band { position: absolute; left: 0; top: 907px; width: 723px; height: 293px;
    background: radial-gradient(ellipse at 60% 50%, #f4ec44, var(--yellow-soft) 70%); }
  .book-front { position: absolute; left: 58px; top: 888px; width: 200px; height: 278px;
    background: linear-gradient(170deg, #f3eb2e, #dcd31f); transform: rotate(-6deg); }

  .contents-heading { position: absolute; left: 232px; top: 884px; width: 450px; height: 41px; background: var(--white);
    border-radius: 0 10px 10px 0; display: flex; align-items: center; padding-left: 54px;
    font-size: 23px; letter-spacing: 1.5px; color: var(--ink); font-weight: 400; white-space: nowrap; }
  .contents-heading strong { font-weight: 800; margin-left: 7px; }
  .contents-list { position: absolute; left: 300px; top: 964px; list-style: none; display: flex; flex-direction: column; gap: 9.5px; }
  .contents-list li { align-self: flex-start; border: 1.5px solid #fff9c8; border-radius: 10px; white-space: nowrap;
    padding: 0 20px 0 12px; height: 18.5px; line-height: 16px; font-weight: 600; font-size: 12.4px; color: var(--pill-text); }
</style>
</head>
<body>
<main class="canvas">
  <div class="book-stack" role="img" aria-label="Stacked yellow paperbacks of the book"></div>
  <div class="book-open" role="img" aria-label="Open book showing the introduction and first chapter pages"></div>
  <div class="book-back" role="img" aria-label="Back cover of the yellow paperback"></div>

  <h1 class="headline">
    <span class="lead">EMBARK ON A</span>
    <span class="accent">MIND-BENDING</span>
    <span class="accent">JOURNEY</span>
    <span class="plain">INTO THE REALM OF</span>
    <span class="topic">QUANTUM</span>
    <span class="topic">PHYSICS</span>
  </h1>

  <div class="badge-audience">
    <span class="top">IDEAL FOR</span>
    <span class="hl">SCIENCE STUDENTS,</span>
    <span>QUANTUM<br>COMPUTING<br>ENTHUSIASTS</span>
  </div>
  <div class="badge-gift">
    <span>PERFECT<br>GIFT FOR THE</span>
    <span class="big">SCIENCE<br>LOVER</span>
  </div>

  <section class="features">
    <article class="feature">
      <div class="feature-title"><span class="light">HISTORY</span><span class="bold">OF QUANTUM<br>MECHANICS</span></div>
      <p class="feature-text">Explore the fascinating history of quantum mechanics and the brilliant minds behind its development</p>
    </article>
    <article class="feature alt">
      <div class="feature-title"><span class="light">FUNDAMENTAL</span><span class="bold">PRINCIPLES OF<br>WAVE-PARTICLE</span></div>
      <p class="feature-text">Grasp the fundamental principles of wave-particle duality, quantum states, and the uncertainty principle</p>
    </article>
    <article class="feature">
      <div class="feature-title"><span class="light">QUANTUM</span><span class="bold">ENTANGLEMENT</span></div>
      <p class="feature-text">Dive into the strange and counterintuitive world of quantum entanglement and its implications for reality itself</p>
    </article>
    <article class="feature alt">
      <div class="feature-title"><span class="light">QUANTUM</span><span class="bold">COMPUTING TO<br>CRYPTOGRAPHY</span></div>
      <p class="feature-text">Learn about the cutting-edge applications of quantum mechanics, from quantum computing to cryptography</p>
    </article>
  </section>

  <div class="yellow-band"></div>
  <div class="book-front" role="img" aria-label="Front cover of the yellow paperback with an atom symbol"></div>

  <h2 class="contents-heading">IN THIS BOOK <strong>YOU WILL FIND</strong></h2>
  <ul class="contents-list">
    <li>The Quantum World Unveiled</li>
    <li>The Mathematical Symphony of Quantum Mechanics</li>
    <li>Beyond Classical Boundaries</li>
    <li>Quantum Mechanics at Work</li>
    <li>Bridging Quantum Mechanics and Relativity</li>
    <li>Quantum Paradoxes and Thought Experiments</li>
    <li>Quantum Mechanics for the Curious Mind</li>
    <li>Quantum Mechanics Demystified - A Practical Guide</li>
  </ul>
</main>
</body>
</html>
```